New tech executive consulting company needs professionally branded document templates

We are a new business selling fractional board advisory and go-to-market consulting services into the Technology space. Tessaly Brink are experts in providing high-quality executive-level leaders on a part-time basis to tech companies in need of their expertise. We work closely with clients to understand their business needs, challenges, and goals, and provides customised solutions to help them succeed. Due to our audience we need the design to have a high quality, executive look and feel.

Our first website is live and can be found at tessalybrink.example. We also already have a logo which I've uploaded. Our brand is clean and uses orange to give it colour and an identity that stands out.

We need some document master templates created so we can create our own presentations (Google Slides & Powerpoint), PDF documents, and Word templates, and ideally also a LinkedIn banner.

```html
<!DOCTYPE html>
<html lang="en">
<head>
<meta charset="utf-8">
<title>Tessaly Brink – Presentation Templates</title>
<link rel="stylesheet" href="https://fonts.googleapis.com/css2?family=Nunito:wght@700;800;900&family=Open+Sans:wght@400;600&display=swap">
<style>
  :root {
    --orange: #ee8650;
    --orange-deep: #d9692f;
    --navy: #253040;
    --ink: #1e2430;
    --grey: #e6e7e9;
    --page: #1d1d1d;
    --white: #ffffff;
  }
  * { box-sizing: border-box; margin: 0; padding: 0; }
  html, body { width: 1200px; height: 4121px; overflow: hidden; background: var(--page); }
  body { position: relative; font-family: "Open Sans", Arial, sans-serif; color: var(--ink); }

  .slide { position: absolute; left: 48px; width: 1098px; height: 616px; background: var(--white); overflow: hidden; }
  .slide > svg.shapes { position: absolute; inset: 0; width: 1098px; height: 616px; }
  .slide--cover { top: 50px; }
  .slide--agenda { top: 731px; }
  .slide--about { top: 1402px; }
  .slide--profile { top: 2067px; }
  .slide--why { top: 2738px; }
  .slide--thanks { top: 3408px; }

  .brand { position: absolute; font-family: "Nunito", Arial, sans-serif; font-weight: 900; color: var(--navy); letter-spacing: 3px; text-transform: uppercase; line-height: 1.1; text-align: center; }
  .brand--light { color: var(--white); }

  .heading { position: absolute; font-family: "Nunito", Arial, sans-serif; font-weight: 900; color: var(--orange); text-transform: uppercase; letter-spacing: 1px; font-size: 50px; line-height: 1; }

  .body-copy { position: absolute; width: 456px; font-size: 15px; line-height: 31.4px; text-align: justify; color: var(--ink); }
  .body-copy p + p { margin-top: 31px; }

  .tagline { position: absolute; right: 55px; top: 274px; text-align: right; font-family: "Nunito", Arial, sans-serif; font-weight: 800; font-size: 30px; line-height: 45px; color: var(--orange); text-transform: uppercase; letter-spacing: .5px; }

  .contact { position: absolute; display: flex; align-items: center; gap: 14px; font-size: 21px; font-weight: 600; color: var(--ink); }
  .contact--right { right: 55px; flex-direction: row-reverse; }
  .contact .dot { width: 38px; height: 38px; border-radius: 50%; background: var(--orange); display: flex; align-items: center; justify-content: center; flex: none; }
  .contact .dot svg { width: 18px; height: 18px; }

  .agenda-title { left: 560px; top: 42px; font-size: 54px; }
  .agenda-item { position: absolute; display: flex; align-items: center; gap: 12px; font-family: "Nunito", Arial, sans-serif; font-weight: 800; font-size: 33px; color: var(--ink); }
  .agenda-item .num { width: 40px; height: 40px; border-radius: 50%; background: var(--orange); color: var(--white); font-size: 18px; display: flex; align-items: center; justify-content: center; }

  .subtitle { position: absolute; left: 53px; top: 104px; font-size: 22px; font-weight: 600; color: var(--ink); }

  .photo-box { position: absolute; left: 560px; top: 45px; width: 483px; height: 486px; }
</style>
</head>
<body>

<!-- Cover -->
<section class="slide slide--cover">
  <svg class="shapes" viewBox="0 0 1098 616" aria-hidden="false">
    <defs>
      <linearGradient id="coverTone" x1="0" y1="0" x2="1" y2="1">
        <stop offset="0" stop-color="#f2a172"/><stop offset="1" stop-color="#d8733d"/>
      </linearGradient>
    </defs>
    <polygon points="730,440 1098,440 1098,616 900,616" fill="#f3f3f4"/>
    <polygon role="img" aria-label="Photo of a smiling consultant team in an office, orange toned" points="0,0 731,0 400,616 0,616" fill="url(#coverTone)"/>
    <polygon points="253,131 305,131 590,616 532,616" fill="var(--navy)"/>
    <polygon points="1098,470 1098,540 1050,616 1000,616" fill="var(--orange)"/>
  </svg>
  <div class="brand" style="right:55px; top:128px; font-size:46px; text-align:right;">Tessaly<br>Brink</div>
  <div class="tagline">Experts in providing<br>executive leadership<br>on demand</div>
  <div class="contact contact--right" style="top:412px;">
    <span class="dot"><svg viewBox="0 0 24 24"><path fill="#fff" d="M3 6h18v12H3z M3 6l9 7 9-7" stroke="#ee8650" stroke-width="1.5"/></svg></span>
    <span>info@tessalybrink.example</span>
  </div>
  <div class="contact contact--right" style="top:468px;">
    <span class="dot"><svg viewBox="0 0 24 24"><path fill="#fff" d="M6.6 10.8a15 15 0 0 0 6.6 6.6l2.2-2.2c.3-.3.7-.4 1-.2 1.1.4 2.3.6 3.6.6.6 0 1 .4 1 1V20c0 .6-.4 1-1 1A17 17 0 0 1 3 4c0-.6.4-1 1-1h3.5c.6 0 1 .4 1 1 0 1.3.2 2.5.6 3.6.1.3 0 .7-.2 1z"/></svg></span>
    <span>+44 7700 900123</span>
  </div>
</section>

<!-- Agenda -->
<section class="slide slide--agenda">
  <svg class="shapes" viewBox="0 0 1098 616">
    <defs>
      <linearGradient id="agendaTone" x1="0" y1="0" x2="1" y2="1">
        <stop offset="0" stop-color="#f0a170"/><stop offset="1" stop-color="#c9662f"/>
      </linearGradient>
    </defs>
    <rect width="1098" height="616" fill="#f4f4f5"/>
    <polygon role="img" aria-label="Photo of a business meeting, navy toned" points="0,0 509,0 80,616 0,616" fill="var(--navy)"/>
    <polygon role="img" aria-label="Photo of a smiling executive at a table, orange toned" points="1040,0 1098,0 1098,616 586,616" fill="url(#agendaTone)"/>
  </svg>
  <div class="brand brand--light" style="left:53px; top:34px; font-size:36px;">Tessaly<br>Brink</div>
  <div class="heading agenda-title">Agenda</div>
  <div class="agenda-item" style="left:507px; top:131px;"><span class="num">01</span>About Us</div>
  <div class="agenda-item" style="left:470px; top:223px;"><span class="num">02</span>Our Team</div>
  <div class="agenda-item" style="left:418px; top:313px;"><span class="num">03</span>Our Services</div>
  <div class="agenda-item" style="left:362px; top:397px;"><span class="num">04</span>Testimonials</div>
  <div class="agenda-item" style="left:299px; top:489px;"><span class="num">05</span>Contact Us</div>
</section>

<!-- About -->
<section class="slide slide--about">
  <svg class="shapes" viewBox="0 0 1098 616">
    <polygon points="925,0 1008,0 592,616 496,616" fill="var(--orange)"/>
    <polygon points="1056,0 1098,0 1098,616 640,616" fill="var(--orange)"/>
  </svg>
  <div class="heading" style="left:53px; top:42px;">About</div>
  <div class="subtitle">The smart way to scale your business</div>
  <div class="body-copy" style="left:53px; top:150px;">
    <p>Tessaly Brink are experts in providing high-quality executive-level leaders on a part-time basis to tech companies in need of their expertise. We work closely with clients to understand their business needs, challenges, and goals, and provides customised solutions to help them succeed.</p>
    <p>Our strategic insights, leadership, and collaborative approach make us a valuable partner for companies looking to drive growth and innovation. We are passionate about helping companies achieve their goals and are committed to providing the highest level of service to our clients.</p>
  </div>
  <div class="brand" style="left:53px; top:520px; font-size:25px;">Tessaly<br>Brink</div>
  <div class="photo-box" role="img" aria-label="Photo of a senior consultant shaking hands across a desk" style="background:linear-gradient(135deg,#dfe6ea,#9aa3a8);"></div>
</section>

<!-- Profile -->
<section class="slide slide--profile">
  <svg class="shapes" viewBox="0 0 1098 616">
    <polygon points="300,250 350,250 576,616 510,616" fill="var(--grey)"/>
    <defs>
      <linearGradient id="profileTone" x1="0" y1="0" x2="1" y2="1">
        <stop offset="0" stop-color="#6b5a4c"/><stop offset=".6" stop-color="#3b4a6a"/><stop offset="1" stop-color="#2c4e86"/>
      </linearGradient>
    </defs>
    <polygon role="img" aria-label="Portrait photo of the founder in a blue blazer" points="0,0 557,0 416,616 0,616" fill="url(#profileTone)"/>
  </svg>
  <div class="heading" style="left:582px; top:42px;">Rowan Ashby</div>
  <div class="body-copy" style="left:586px; top:109px;">
    <p>Rowan Ashby is a highly accomplished business leader with extensive experience in executive-level leadership and strategy. As the founder of Tessaly Brink, Rowan brings his years of experience in the technology industry to help companies achieve their goals.</p>
    <p>Throughout his career, Rowan has held executive positions in companies ranging from startups to large corporations. He has a deep understanding of the tech industry and has helped companies at all stages of maturity drive significant growth and innovation.</p>
  </div>
  <div class="brand" style="right:55px; top:520px; font-size:25px;">Tessaly<br>Brink</div>
</section>

<!-- Why choose us -->
<section class="slide slide--why">
  <svg class="shapes" viewBox="0 0 1098 616">
    <polygon points="925,0 1008,0 592,616 496,616" fill="var(--orange)"/>
    <polygon points="1056,0 1098,0 1098,616 640,616" fill="var(--navy)"/>
  </svg>
  <div class="heading" style="left:53px; top:42px;">Why choose us</div>
  <div class="body-copy" style="left:53px; top:108px;">
    <p>At vero eos et accusamus et iusto odio dignissimos ducimus qui blanditiis praesentium voluptatum deleniti atque corrupti quos dolores et quas molestias excepturi sint occaecati cupiditate non provident, similique sunt in culpa qui officia deserunt mollitia animi, id est laborum et dolorum fuga. Et harum quidem rerum facilis est et expedita distinctio.</p>
    <p>Nam libero tempore, cum soluta nobis est eligendi optio cumque nihil impedit quo minus id quod maxime placeat facere possimus, omnis voluptas assumenda est, omnis dolor repellendus.</p>
  </div>
  <div class="brand" style="left:53px; top:520px; font-size:25px;">Tessaly<br>Brink</div>
  <div class="photo-box" role="img" aria-label="Photo of a laughing consultant in a meeting" style="background:linear-gradient(135deg,#c98a5a,#eceae6 55%,#5b4a44);"></div>
</section>

<!-- Thank you -->
<section class="slide slide--thanks">
  <svg class="shapes" viewBox="0 0 1098 616">
    <defs>
      <linearGradient id="thanksTone" x1="0" y1="0" x2="1" y2="1">
        <stop offset="0" stop-color="#e88a52"/><stop offset="1" stop-color="#b8612e"/>
      </linearGradient>
      <linearGradient id="thanksPhoto" x1="0" y1="0" x2="1" y2="1">
        <stop offset="0" stop-color="#c9c2b8"/><stop offset=".5" stop-color="#9a6a45"/><stop offset="1" stop-color="#3d3430"/>
      </linearGradient>
    </defs>
    <polygon role="img" aria-label="Photo of colleagues reviewing documents, orange toned" points="336,0 1098,0 1098,616 690,616" fill="url(#thanksTone)"/>
    <polygon role="img" aria-label="Photo of a smiling colleague taking notes" points="736,0 1098,0 1098,616 900,616" fill="url(#thanksPhoto)"/>
    <polygon points="800,288 850,288 640,616 584,616" fill="var(--navy)"/>
  </svg>
  <div class="brand" style="left:53px; top:168px; font-size:50px; text-align:left;">Tessaly<br>Brink</div>
  <div class="heading" style="left:53px; top:306px;">Thank you</div>
  <div class="contact" style="left:53px; top:386px;">
    <span class="dot"><svg viewBox="0 0 24 24"><path fill="#fff" d="M3 6h18v12H3z M3 6l9 7 9-7" stroke="#ee8650" stroke-width="1.5"/></svg></span>
    <span>info@tessalybrink.example</span>
  </div>
  <div class="contact" style="left:53px; top:447px;">
    <span class="dot"><svg viewBox="0 0 24 24"><path fill="#fff" d="M6.6 10.8a15 15 0 0 0 6.6 6.6l2.2-2.2c.3-.3.7-.4 1-.2 1.1.4 2.3.6 3.6.6.6 0 1 .4 1 1V20c0 .6-.4 1-1 1A17 17 0 0 1 3 4c0-.6.4-1 1-1h3.5c.6 0 1 .4 1 1 0 1.3.2 2.5.6 3.6.1.3 0 .7-.2 1z"/></svg></span>
    <span>+44 7700 900123</span>
  </div>
</section>

</body>
</html>
```